I need a website, primarily a landing page, for my company, Morrow Vantage. A sales training and cons

I need a web design/landing page for a new sales training and consulting company, morrow vantage. We perform "sales experiments" aimed at each individual or team, where we assist in helping them identify their strengths, through a series of "sales experiments" that we can tailor based on the individual and what they're trying to accomplish.

```html
<!DOCTYPE html>
<html lang="en">
<head>
<meta charset="utf-8">
<title>Morrow Vantage — Sales Training &amp; Consulting</title>
<link href="https://fonts.googleapis.com/css2?family=Lato:wght@400;700;900&display=swap" rel="stylesheet">
<style>
:root{
  --brand:#215b98;
  --brand-dark:#1a4a7d;
  --ink:#1d1d1f;
  --body:#555a60;
  --muted:#777;
  --line:#b9bcc0;
  --white:#ffffff;
}
*{margin:0;padding:0;box-sizing:border-box}
html,body{width:1200px;height:3468px;overflow:hidden;background:var(--white)}
body{position:relative;font-family:'Lato',sans-serif;color:var(--ink)}
.abs{position:absolute}

/* header */
.topbar{top:18px;right:110px;font-size:15px;font-weight:700;color:var(--ink);display:flex;align-items:center;gap:10px}
.topbar svg{width:14px;height:14px;fill:var(--brand)}
.topbar .sep{color:var(--muted);font-weight:400}
.nav{top:66px;right:105px;display:flex;gap:33px;font-size:15px;font-weight:700;text-transform:uppercase;align-items:center}
.nav a{color:var(--ink);text-decoration:none}
.nav a.active{color:var(--brand)}
.nav svg{width:15px;height:15px}

.hero{top:111px;left:0;width:1200px;height:629px;background:linear-gradient(110deg,#c79a5e 0%,#8b6d50 22%,#4a5665 45%,#5f7590 70%,#c9d3dc 100%)}
.brand-disc{top:-138px;left:104px;width:268px;height:406px;border-radius:0 0 134px 134px;background:var(--white);z-index:3;display:flex;flex-direction:column;align-items:center;justify-content:flex-end;padding-bottom:84px}
.brand-disc .name{font-size:29px;font-weight:900;color:var(--brand);text-transform:uppercase;letter-spacing:.5px;line-height:1.1;text-align:center}
.hero h1{position:absolute;top:175px;left:0;width:1200px;text-align:center;color:var(--white);font-size:76px;font-weight:900;line-height:86px;text-transform:uppercase}
.hero .cta{position:absolute;top:388px;left:458px;width:282px;height:62px;border:2px solid var(--white);border-radius:31px;color:var(--white);font-size:16px;font-weight:700;text-transform:uppercase;display:flex;align-items:center;justify-content:center;letter-spacing:.5px}
.dots{position:absolute;top:557px;left:567px;display:flex;gap:5px}
.dots span{width:13px;height:13px;border-radius:50%;border:2px solid var(--white)}
.dots span.on{background:var(--white)}

/* welcome */
.section-title{width:1200px;left:0;text-align:center;font-size:42px;font-weight:700;text-transform:uppercase;color:var(--ink)}
.lead{font-size:14.5px;line-height:30px;color:var(--body);text-align:center}
.video{top:1031px;left:398px;width:404px;height:264px;background:linear-gradient(135deg,#3a4d6e,#7f8ea8 50%,#2b3549);box-shadow:0 4px 14px rgba(0,0,0,.35)}
.video .play{position:absolute;left:172px;top:102px;width:60px;height:60px;border-radius:50%;background:#111;display:flex;align-items:center;justify-content:center}

/* experiments */
.experiments{top:1417px;left:0;width:1200px;height:601px;overflow:hidden;background:linear-gradient(120deg,#eef1f5 0%,#b5c2d4 30%,#6b7f99 50%,#2a2c31 80%)}
.experiments .disc{position:absolute;left:580px;top:-38px;width:680px;height:680px;border-radius:50%;background:var(--white)}
.exp-body{position:absolute;left:700px;width:390px;text-align:center}
.btn{background:var(--brand);color:var(--white);font-weight:700;font-size:15px;text-transform:uppercase;border-radius:30px;display:flex;align-items:center;justify-content:center}

/* services */
.service{width:230px;text-align:center}
.service svg{width:72px;height:72px;fill:var(--brand)}
.service h3{margin-top:18px;font-size:26px;font-weight:700}
.service p{margin-top:14px;font-size:14.5px;line-height:25px;color:var(--body)}

/* contact */
.contact{top:2550px;left:0;width:1200px;height:567px;overflow:hidden;background:linear-gradient(100deg,#dfe3e8 0%,#c8b8a4 45%,#8b7a6a 70%,#e9eaec 100%)}
.contact .disc{position:absolute;left:98px;top:-22px;width:564px;height:564px;border-radius:50%;background:var(--white)}
.contact h2{position:absolute;left:111px;top:63px;font-size:40px;font-weight:700;text-transform:uppercase}
.field{position:absolute;border:1.5px solid #9a9da2;font-size:14px;color:#333;padding:10px 14px;background:var(--white)}

/* footer */
.social{top:3223px;left:488px;display:flex;gap:8px}
.social span{width:50px;height:50px;border-radius:50%;border:1.5px solid var(--line)}
.foot-line{left:0;width:1200px;text-align:center;font-size:14.5px;color:#444}
.foot-line svg{width:13px;height:13px;fill:var(--brand);vertical-align:-1px;margin-right:6px}
.foot-line .sep{margin:0 14px;color:#888}
</style>
</head>
<body>

<div class="abs topbar">
  <svg viewBox="0 0 24 24"><path d="M6.6 10.8a15 15 0 0 0 6.6 6.6l2.2-2.2c.3-.3.7-.4 1-.2 1.1.4 2.3.6 3.6.6.6 0 1 .4 1 1V20c0 .6-.4 1-1 1C10.6 21 3 13.4 3 4c0-.6.4-1 1-1h3.5c.6 0 1 .4 1 1 0 1.3.2 2.5.6 3.6.1.3 0 .7-.2 1z"/></svg>
  <span>1 555 204 7788</span><span class="sep">|</span>
  <svg viewBox="0 0 24 24"><path d="M2 5h20v14H2z"/><path d="M2 5l10 8 10-8" fill="none" stroke="#fff" stroke-width="2"/></svg>
  <span>info@morrowvantage.com</span>
</div>
<nav class="abs nav">
  <a class="active" href="#">Home</a><a href="#">About Us</a><a href="#">What We Do</a><a href="#">News &amp; Insights</a><a href="#">Contact</a>
  <svg viewBox="0 0 24 24"><circle cx="10" cy="10" r="6.5" fill="none" stroke="#1d1d1f" stroke-width="3"/><path d="M15 15l6 6" stroke="#1d1d1f" stroke-width="3.5"/></svg>
</nav>

<section class="abs hero" role="img" aria-label="Mountain peaks rising above golden morning clouds">
  <h1>Success.<br>It’s in your DNA</h1>
  <div class="cta">Request a consultation</div>
  <div class="dots"><span class="on"></span><span></span><span></span><span></span></div>
</section>
<div class="abs brand-disc">
  <div class="name">Morrow<br>Vantage</div>
</div>

<h2 class="abs section-title" style="top:822px">Welcome to Morrow Vantage</h2>
<p class="abs lead" style="top:898px;left:243px;width:717px">Nemo enim ipsam voluptatem quia voluptas sit aspernatur aut odit aut fugit, sed quia consequuntur magni dolores eos qui ratione voluptatem sequi nesciunt. Neque porro quisquam est, qui dolorem ipsum quia dolor sit amet, consectetur, adipisci velit, sed quia non numquam eius modi tempora.</p>
<div class="abs video" role="img" aria-label="Video still of a hand touching a glowing DNA hologram above a tablet">
  <div class="play"><svg width="24" height="26" viewBox="0 0 24 26"><path d="M4 1l19 12L4 25z" fill="#fff"/></svg></div>
</div>

<section class="abs experiments" role="img" aria-label="Hand with a pen reviewing printed sales charts">
  <div class="disc"></div>
</section>
<svg class="abs" style="top:1483px;left:866px" width="58" height="46" viewBox="0 0 58 46" fill="#215b98">
  <rect x="0" y="42" width="58" height="4"/><rect x="0" y="0" width="4" height="46"/>
  <rect x="10" y="22" width="6" height="17"/><rect x="20" y="12" width="6" height="27"/><rect x="30" y="18" width="6" height="21"/><rect x="40" y="8" width="6" height="31"/><rect x="50" y="26" width="6" height="13"/>
</svg>
<h2 class="abs exp-body" style="top:1570px;font-size:42px;font-weight:700;text-transform:uppercase;left:660px;width:470px">Sales Experiments</h2>
<p class="abs exp-body lead" style="top:1640px">Sed ut perspiciatis unde omnis iste natus error sit vo luptatem accusantium doloremque laudantium, totam rem aperiam, eaque ipsa quae ab illo inventore veritatis et qua si architecto beatae vitae numquam.</p>
<div class="abs btn" style="top:1794px;left:775px;width:243px;height:58px">Our sales perspective</div>

<h2 class="abs section-title" style="top:2116px">What We Do</h2>
<div class="abs service" style="top:2223px;left:100px">
  <svg viewBox="0 0 72 72"><path d="M30 8C15 8 4 17 4 28c0 6 3 11 8 14l-3 10 11-7c3 1 6 1 10 1 15 0 26-9 26-20S45 8 30 8zm0 5c12 0 21 7 21 15s-9 15-21 15c-3 0-6 0-9-1l-5 3 1-5c-5-3-8-7-8-12 0-8 9-15 21-15z"/><path d="M58 26c6 3 10 9 10 15 0 5-3 9-7 12l3 9-10-6c-3 1-6 1-9 1-8 0-14-3-18-7 14 0 29-8 31-24z"/></svg>
  <h3>Consulting</h3>
  <p>Nemo enim ipsam voluptatem quia voluptas sit aspernatur aodit aut fugit, sed quia con.</p>
</div>
<div class="abs service" style="top:2223px;left:354px">
  <svg viewBox="0 0 72 72"><circle cx="28" cy="42" r="16"/><g stroke="#215b98" stroke-width="7"><path d="M28 20v44M6 42h44M12 26l32 32M44 26L12 58"/></g><circle cx="28" cy="42" r="6" fill="#fff"/><circle cx="54" cy="18" r="10"/><g stroke="#215b98" stroke-width="5"><path d="M54 4v28M40 18h28M44 8l20 20M64 8L44 28"/></g><circle cx="54" cy="18" r="4" fill="#fff"/></svg>
  <h3>Sales Training</h3>
  <p>Nemo enim ipsam voluptatem quia voluptas sit aspernatur aodit aut fugit, sed quia con.</p>
</div>
<div class="abs service" style="top:2223px;left:609px">
  <svg viewBox="0 0 72 72"><rect x="2" y="8" width="5" height="58"/><rect x="2" y="61" width="68" height="5"/><path d="M10 52l16-18 12 10 18-20" fill="none" stroke="#215b98" stroke-width="6"/><path d="M48 16h16v16z"/></svg>
  <h3>Coaching</h3>
  <p>Nemo enim ipsam voluptatem quia voluptas sit aspernatur aodit aut fugit, sed quia con.</p>
</div>
<div class="abs service" style="top:2223px;left:863px">
  <svg viewBox="0 0 72 72"><path d="M36 6l6 7 9-3 2 9 9 2-3 9 7 6-7 6 3 9-9 2-2 9-9-3-6 7-6-7-9 3-2-9-9-2 3-9-7-6 7-6-3-9 9-2 2-9 9 3z"/></svg>
  <h3>Sales Qualifications</h3>
  <p>Nemo enim ipsam voluptatem quia voluptas sit aspernatur aodit aut fugit, sed quia con.</p>
</div>

<section class="abs contact" role="img" aria-label="Hand pointing at a printed pie chart and bar graphs on a desk">
  <div class="disc"></div>
  <h2>Get in Touch</h2>
  <div class="field" style="left:111px;top:141px;width:227px;height:40px">First Name</div>
  <div class="field" style="left:347px;top:141px;width:224px;height:40px">Last Name</div>
  <div class="field" style="left:111px;top:197px;width:227px;height:40px">Email Address</div>
  <div class="field" style="left:347px;top:197px;width:224px;height:40px">Phone Number</div>
  <div class="field" style="left:111px;top:248px;width:460px;height:81px">Message</div>
  <div class="btn" style="position:absolute;left:111px;top:359px;width:146px;height:55px">Contact Us</div>
</section>

<div class="abs social" aria-label="Social media links"><span></span><span></span><span></span><span></span></div>
<p class="abs foot-line" style="top:3312px">
  <svg viewBox="0 0 24 24"><path d="M12 2a7 7 0 0 0-7 7c0 5 7 13 7 13s7-8 7-13a7 7 0 0 0-7-7zm0 9.5A2.5 2.5 0 1 1 12 6.5a2.5 2.5 0 0 1 0 5z"/></svg>48 Harrow Lane Brookfield, K2P 1L6<span class="sep">|</span><svg viewBox="0 0 24 24"><path d="M6.6 10.8a15 15 0 0 0 6.6 6.6l2.2-2.2c.3-.3.7-.4 1-.2 1.1.4 2.3.6 3.6.6.6 0 1 .4 1 1V20c0 .6-.4 1-1 1C10.6 21 3 13.4 3 4c0-.6.4-1 1-1h3.5c.6 0 1 .4 1 1 0 1.3.2 2.5.6 3.6.1.3 0 .7-.2 1z"/></svg>1 555 204 7788<span class="sep">|</span><svg viewBox="0 0 24 24"><path d="M2 5h20v14H2z"/><path d="M2 5l10 8 10-8" fill="none" stroke="#fff" stroke-width="2"/></svg>info@morrowvantage.com
</p>
<p class="abs foot-line" style="top:3349px">Help<span class="sep">|</span>FAQ<span class="sep">|</span>Support<span class="sep">|</span>Sitemap<span class="sep">|</span>Terms Of Use<span class="sep">|</span>Privacy Statement</p>
<p class="abs foot-line" style="top:3388px">Morrow Vantage © 2018 All rights reserved.</p>

</body>
</html>
```